** Wanted ** Wordpress web design for scaffolding rental and construction company

We need a website design and must be functional to show a basic overview of what our company offers as a service. We have a domain name and a logo but we need web design. This web site should have another scaffolding rental page for construction and renovation as well as a quote section where customers can enter their personal information and also upload photos. The site% 26quot; www.brindlework.com% 26quot; should be intuitive, clear and classy ... The logo must be found on the site in several ways.

Target Market(s)

Professional and no professional

Coding

Coded - Design and coding required

Number of Pages Required

3 page

Font styles to use
Serif
Sans Serif
Decorative
Script

Requirements
Must have
• Our logo
Nice to have
• Slogan:% 26quot; The height% 26 # 224; port% 26 # 233; e hand% 26quot;

```html
<!DOCTYPE html>
<html lang="en">
<head>
<meta charset="utf-8">
<title>Brindlework — Scaffolding Rental &amp; Construction</title>
<link rel="stylesheet" href="https://fonts.googleapis.com/css2?family=Signika:wght@500;600&family=Lato:wght@400;700;900&family=Montserrat:wght@400&display=swap">
<style>
:root{
  --orange:#ee7419;
  --ink:#1a1a1a;
  --dark:#1e1e1e;
  --grey:#ececec;
  --text:#444;
  --muted:#555;
  --white:#fff;
}
*{box-sizing:border-box;margin:0;padding:0}
html,body{width:1200px;height:3690px;overflow:hidden}
body{position:relative;background:var(--white);font-family:"Lato",sans-serif;color:var(--text)}
.abs{position:absolute}
.heading{font-family:"Signika",sans-serif;font-weight:600;color:var(--ink);letter-spacing:1px;text-transform:uppercase}
.btn{position:absolute;display:flex;align-items:center;justify-content:center;font-family:"Lato",sans-serif;font-weight:900;font-size:15px;letter-spacing:1px;color:var(--white);text-transform:uppercase;clip-path:polygon(12% 0,100% 0,88% 100%,0 100%)}
.btn-dark{background:var(--ink)}
.btn-orange{background:var(--orange)}

/* header */
.topbar{left:0;top:0;width:1200px;height:155px;background:var(--dark)}
.brand{position:absolute;display:flex;align-items:center;gap:10px;font-family:"Signika",sans-serif;font-weight:600;color:var(--orange);text-transform:uppercase;letter-spacing:1px}
.brand .mark{width:16px;height:16px;background:var(--orange)}
.header-brand{left:76px;top:88px;font-size:26px}
.contact-top{right:76px;top:50px;color:var(--white);text-align:right}
.contact-top .phone{font-family:"Signika",sans-serif;font-weight:600;font-size:26px;letter-spacing:1px;display:flex;align-items:center;gap:20px;justify-content:flex-end}
.contact-top .mail{font-size:16px;font-weight:700;margin-top:6px;display:flex;align-items:center;gap:16px;justify-content:flex-end}
.nav{left:0;top:155px;width:1200px;height:54px;background:#000;display:flex;align-items:center}
.nav ul{list-style:none;display:flex;margin-left:79px;height:100%}
.nav li{display:flex;align-items:center;padding:0 19px;font-size:13.5px;font-weight:700;color:var(--white);letter-spacing:.5px;text-transform:uppercase}
.nav li.active{background:var(--orange);clip-path:polygon(12% 0,100% 0,100% 100%,0 100%);padding:0 20px 0 20px}
.nav .search{position:absolute;right:72px;top:17px}

/* hero */
.hero-photo{left:0;top:209px;width:1200px;height:541px;background:linear-gradient(180deg,#5c6a8a 0%,#c9889a 35%,#f0a060 65%,#e08d2a 100%)}
.hero-panel{left:641px;top:349px;width:485px;height:262px;background:rgba(70,70,70,.72);text-align:right;padding:24px 22px 0 0;color:var(--white)}
.hero-panel h1{font-family:"Signika",sans-serif;font-weight:600;font-size:62px;line-height:1;letter-spacing:2px;text-transform:uppercase}
.hero-panel p{font-family:"Signika",sans-serif;font-weight:500;font-size:25px;line-height:34px;margin-top:12px}
.hero-dot{left:566px;top:696px;width:11px;height:11px;border-radius:50%;background:var(--white)}

/* welcome */
.welcome-title{left:386px;top:848px;width:428px;height:52px;border:3px solid var(--orange);display:flex;align-items:center;justify-content:center;font-size:27px}
.welcome-text{left:80px;top:938px;width:1040px;text-align:center;font-family:"Montserrat",sans-serif;font-size:16.5px;line-height:32.5px;color:var(--muted)}

/* services */
.services-bg{left:0;top:1191px;width:1200px;height:639px}
.section-title{width:1200px;left:0;text-align:center;font-size:28px}
.card{background:var(--white);width:511px;height:447px;text-align:center}
.card .photo{position:absolute;left:16px;top:16px;width:481px;height:204px}
.card h3{position:absolute;top:245px;width:100%;font-family:"Signika",sans-serif;font-weight:600;font-size:21px;color:var(--orange);letter-spacing:1px;text-transform:uppercase}
.card p{position:absolute;top:278px;left:24px;right:24px;font-size:14.5px;line-height:26px;color:#333}
.card .btn{left:157px;top:376px;width:198px;height:48px}

/* blog */
.post{width:333px;text-align:center}
.post .photo{width:333px;height:201px}
.post h3{margin-top:24px;font-family:"Signika",sans-serif;font-weight:600;font-size:21px;line-height:30px;color:var(--orange);letter-spacing:1px;text-transform:uppercase}
.post p{margin-top:12px;font-size:14.5px;line-height:23px;color:#333}
.post .more{margin-top:10px;font-size:14px;font-weight:900;color:var(--ink);letter-spacing:1px}

/* reviews */
.reviews-bg{left:0;top:2426px;width:1200px;height:409px;background:linear-gradient(135deg,#3a3a3a 0%,#2b2b2b 50%,#3d3a33 100%)}
.review{width:340px;text-align:center;color:#d8d8d8}
.review .quote{font-family:"Signika",sans-serif;font-weight:600;font-size:50px;line-height:40px;color:var(--white);height:36px}
.review p{margin-top:8px;font-size:15.5px;line-height:26px}
.review .stars{margin-top:16px;color:#f5a623;font-size:15px;letter-spacing:4px}
.review .name{margin-top:2px;font-weight:900;font-size:14px;letter-spacing:1px;color:var(--white)}

/* quote form */
.field{background:var(--grey);font-size:13.5px;color:#555;padding:0 16px;display:flex;align-items:center;justify-content:space-between}
.field.message{align-items:flex-start;padding-top:14px}

/* footer */
.footer-bg{left:0;top:3308px;width:1200px;height:382px;background:var(--grey)}
.foot-col h4{font-family:"Signika",sans-serif;font-weight:600;font-size:16px;letter-spacing:1px;color:var(--ink);text-transform:uppercase}
.foot-col ul{list-style:none;margin-top:10px}
.foot-col li{font-size:13.5px;line-height:27.5px;color:#333}
.foot-contact li{display:flex;align-items:center;gap:16px}
.foot-brand{font-family:"Signika",sans-serif;font-weight:600;font-size:16px;color:var(--orange);letter-spacing:1px;margin-top:8px}
.footer-brand{left:76px;top:3546px;font-size:22px;color:var(--white)}
.footer-brand .mark{background:var(--white)}
.copyright{left:76px;top:3598px;font-size:12.5px;line-height:20px;color:var(--white)}
</style>
</head>
<body>

<!-- header -->
<header>
  <div class="abs topbar"></div>
  <svg class="abs" style="left:0;top:0" width="1200" height="155" aria-hidden="true">
    <polygon points="830,0 1200,0 1200,155 458,155" fill="#ee7419"/>
  </svg>
  <div class="brand header-brand"><span class="mark"></span>Brindlework</div>
  <div class="abs contact-top">
    <div class="phone">
      <svg width="20" height="20" viewBox="0 0 24 24" aria-hidden="true"><path fill="#fff" d="M6.6 10.8a15.1 15.1 0 0 0 6.6 6.6l2.2-2.2a1 1 0 0 1 1-.25 11.4 11.4 0 0 0 3.6.57 1 1 0 0 1 1 1V20a1 1 0 0 1-1 1A17 17 0 0 1 3 4a1 1 0 0 1 1-1h3.5a1 1 0 0 1 1 1c0 1.25.2 2.45.57 3.57a1 1 0 0 1-.25 1z"/></svg>
      1-800-555-0142
    </div>
    <div class="mail">
      <svg width="16" height="12" viewBox="0 0 16 12" aria-hidden="true"><rect width="16" height="12" fill="#fff"/><path d="M0 0l8 6 8-6" stroke="#ee7419" stroke-width="1.5" fill="none"/></svg>
      info@brindlework.com
    </div>
  </div>
  <nav class="abs nav">
    <ul>
      <li class="active">Home</li><li>About</li><li>Services</li><li>Our Work</li><li>Blog</li><li>Request a Quote</li><li>Contact</li>
    </ul>
    <svg class="search" width="18" height="18" viewBox="0 0 18 18" aria-hidden="true"><circle cx="7.5" cy="7.5" r="5.5" stroke="#fff" stroke-width="2.2" fill="none"/><line x1="11.5" y1="11.5" x2="16" y2="16" stroke="#fff" stroke-width="2.4"/></svg>
  </nav>
</header>

<!-- hero -->
<section>
  <div class="abs hero-photo" role="img" aria-label="Workers in silhouette on scaffolding against a sunset sky"></div>
  <div class="abs hero-panel">
    <h1>Brindlework</h1>
    <p>Fusce mollis tellus urna, at venenatis<br>erat viverra vel ligula eget.</p>
  </div>
  <div class="btn btn-orange" style="left:849px;top:531px;width:251px;height:48px;font-size:18px">Request a Quote</div>
  <div class="abs hero-dot"></div>
</section>

<!-- welcome -->
<section>
  <div class="abs heading welcome-title">Welcome to Our Website</div>
  <p class="abs welcome-text">Etiam a lacus euismod, porttitor enim sit amet, mollis lacus. Integer tincidunt, arcu ac hendrerit fermentum, ex leo varius erat, a fermentum nisl velit vitae risus. Maecenas nec ante vitae purus bibendum aliquam uisque a lobortis arcu, a tempor dolor. Nunc consectetur mollis arcu egestas mattis.</p>
  <div class="btn btn-dark" style="left:501px;top:1072px;width:199px;height:48px">Read More</div>
</section>

<!-- services -->
<section>
  <svg class="abs services-bg" width="1200" height="639" aria-hidden="true">
    <rect width="1200" height="639" fill="#ececec"/>
    <polygon points="1200,0 1200,639 0,639 0,635" fill="#ee7419"/>
  </svg>
  <h2 class="abs heading section-title" style="top:1246px">Our Services</h2>
  <article class="abs card" style="left:76px;top:1309px">
    <div class="photo" role="img" aria-label="Workers in hard hats and safety vests facing scaffolding" style="background:linear-gradient(180deg,#9aa3ab 0%,#7d7a6e 55%,#8a8a3a 100%)"></div>
    <h3>Scaffolding Rental</h3>
    <p>Vestibulum ante ipsum primis in faucibus orci luctus et ultrices posuere ermentum nisl velit vitae risus. Maecenas nec ante vitae purus bibendum aliquam obortis arcu.</p>
    <div class="btn btn-dark">Read More</div>
  </article>
  <article class="abs card" style="left:614px;top:1309px">
    <div class="photo" role="img" aria-label="Concrete building under construction with cranes and scaffolding" style="background:linear-gradient(180deg,#8fb0d6 0%,#a9a59c 50%,#6f6a60 100%)"></div>
    <h3>Construction</h3>
    <p>Vestibulum ante ipsum primis in faucibus orci luctus et ultrices posuere ermentum nisl velit vitae risus. Maecenas nec ante vitae purus bibendum aliquam obortis arcu.</p>
    <div class="btn btn-dark">Read More</div>
  </article>
</section>

<!-- blog -->
<section>
  <h2 class="abs heading section-title" style="top:1896px">Blog Posts</h2>
  <article class="abs post" style="left:76px;top:1953px">
    <div class="photo" role="img" aria-label="Construction site with red crane and steel frame" style="background:linear-gradient(180deg,#3f7fc9 0%,#8aa6c4 45%,#9b8b74 100%)"></div>
    <h3>Nam fermentum vestibulum<br>purus id aliquet</h3>
    <p>Duis aliquam nibh a dui iaculis viverra id a velit. Vivamus egestas risus in magna varius commodo. Sed semper viverra egestas. Etiam pretium porttitor lectus,...</p>
    <div class="more">READ MORE</div>
  </article>
  <article class="abs post" style="left:434px;top:1953px">
    <div class="photo" role="img" aria-label="Workers in safety vests in front of scaffolding" style="background:linear-gradient(180deg,#b5bcc2 0%,#6d6c66 55%,#8a8a40 100%)"></div>
    <h3>Nam fermentum vestibulum<br>purus id aliquet</h3>
    <p>Duis aliquam nibh a dui iaculis viverra id a velit. Vivamus egestas risus in magna varius commodo. Sed semper viverra egestas. Etiam pretium porttitor lectus,...</p>
    <div class="more">READ MORE</div>
  </article>
  <article class="abs post" style="left:793px;top:1953px">
    <div class="photo" role="img" aria-label="Building under construction with tower crane" style="background:linear-gradient(180deg,#3c7ccc 0%,#93a9c2 45%,#a58a6a 100%)"></div>
    <h3>Nam fermentum vestibulum<br>purus id aliquet</h3>
    <p>Duis aliquam nibh a dui iaculis viverra id a velit. Vivamus egestas risus in magna varius commodo. Sed semper viverra egestas. Etiam pretium porttitor lectus,...</p>
    <div class="more">READ MORE</div>
  </article>
</section>

<!-- reviews -->
<section>
  <div class="abs reviews-bg" role="img" aria-label="Darkened photo of workers on a construction site"></div>
  <h2 class="abs heading section-title" style="top:2478px;color:#fff">Customer Reviews</h2>
  <div class="abs review" style="left:72px;top:2560px">
    <div class="quote">&ldquo;</div>
    <p>&ldquo;Vestibulum luctus magna vitae dolor fermentum, varius interdum lorem euismod. Nunc quis enim non nisl dignissim porta et ut nunc.&rdquo;</p>
    <div class="stars">★★★★★</div>
    <div class="name">AVERY</div>
  </div>
  <div class="abs review" style="left:432px;top:2560px">
    <div class="quote">&ldquo;</div>
    <p>&ldquo;Vestibulum luctus magna vitae dolor fermentum, varius interdum lorem euismod. Nunc quis enim non nisl dignissim porta et ut nunc.&rdquo;</p>
    <div class="stars">★★★★★</div>
    <div class="name">AVERY</div>
  </div>
  <div class="abs review" style="left:792px;top:2560px">
    <div class="quote">&ldquo;</div>
    <p>&ldquo;Vestibulum luctus magna vitae dolor fermentum, varius interdum lorem euismod. Nunc quis enim non nisl dignissim porta et ut nunc.&rdquo;</p>
    <div class="stars">★★★★★</div>
    <div class="name">AVERY</div>
  </div>
</section>

<!-- quote form -->
<section>
  <h2 class="abs heading section-title" style="top:2895px">Request a Quote</h2>
  <div class="abs field" style="left:302px;top:2977px;width:285px;height:39px">Name</div>
  <div class="abs field" style="left:614px;top:2977px;width:287px;height:39px">Email Address</div>
  <div class="abs field" style="left:302px;top:3026px;width:285px;height:39px">Phone No</div>
  <div class="abs field" style="left:614px;top:3026px;width:287px;height:39px">Upload Photo
    <svg width="14" height="14" viewBox="0 0 14 14" aria-hidden="true"><path d="M7 1l4 4H8.5v4h-3V5H3z" fill="#444"/><rect x="1" y="11" width="12" height="2" fill="#444"/></svg>
  </div>
  <div class="abs field message" style="left:302px;top:3076px;width:599px;height:97px">Message</div>
  <div class="btn btn-orange" style="left:501px;top:3196px;width:199px;height:48px;font-size:18px">Submit</div>
</section>

<!-- footer -->
<footer>
  <svg class="abs footer-bg" width="1200" height="382" aria-hidden="true">
    <rect width="1200" height="382" fill="#ececec"/>
    <polygon points="0,43 645,382 0,382" fill="#ee7419"/>
  </svg>
  <div class="brand footer-brand abs"><span class="mark"></span>Brindlework</div>
  <div class="abs copyright">Copyright © 2020, Brindlework<br>All Right Reserved</div>

  <div class="abs foot-col" style="left:344px;top:3370px">
    <h4>Site Map</h4>
    <ul><li>Home</li><li>About</li><li>Services</li><li>Our Work</li></ul>
  </div>
  <div class="abs foot-col" style="left:464px;top:3370px">
    <h4>&nbsp;</h4>
    <ul><li>Blog</li><li>Request A Quote</li><li>Contact</li></ul>
  </div>
  <div class="abs foot-col" style="left:636px;top:3370px">
    <h4>Resources</h4>
    <ul><li>Etiam a lacus euismod</li><li>Porttitor enim sit</li><li>Mollis lacus</li><li>Integer tincidunt</li><li>Arcu ac hendrerit fermentum</li></ul>
  </div>
  <div class="abs foot-col foot-contact" style="left:898px;top:3370px">
    <h4>Contact Info</h4>
    <div class="foot-brand">BRINDLEWORK</div>
    <ul style="margin-top:2px">
      <li style="line-height:21px;display:block">412 Harbor Line Rd<br>Fairview, VA 22000</li>
      <li><svg width="14" height="14" viewBox="0 0 24 24" aria-hidden="true"><path fill="#222" d="M6.6 10.8a15.1 15.1 0 0 0 6.6 6.6l2.2-2.2a1 1 0 0 1 1-.25 11.4 11.4 0 0 0 3.6.57 1 1 0 0 1 1 1V20a1 1 0 0 1-1 1A17 17 0 0 1 3 4a1 1 0 0 1 1-1h3.5a1 1 0 0 1 1 1c0 1.25.2 2.45.57 3.57a1 1 0 0 1-.25 1z"/></svg>1-800-555-0142</li>
      <li><svg width="14" height="14" viewBox="0 0 14 14" aria-hidden="true"><rect x="1" y="5" width="12" height="8" fill="#222"/><rect x="3" y="1" width="8" height="5" fill="none" stroke="#222" stroke-width="1.5"/></svg>1-800-555-0198</li>
      <li><svg width="14" height="11" viewBox="0 0 16 12" aria-hidden="true"><rect width="16" height="12" fill="#222"/><path d="M0 0l8 6 8-6" stroke="#ececec" stroke-width="1.5" fill="none"/></svg>hello@brindlework.com</li>
    </ul>
  </div>
</footer>

</body>
</html>
```